Web Site Design for a Finance (lending) Company

We are opening a new subsidiary that focuses on lending money in the real estate industry. We need a web site designed to represent the business.

The business is lending money to real estate investors. A typical client/borrower will be looking to borrow money to buy a house, renovate it and then sell it at a profit, all within 12 months or less.

Company name is RTV Finance. Our logo is attached.

Attached is a general outline for the web site. We're working on writing more text for each page but this should give you enough to get started with some ideas.

Competitor web site that I like a lot (as an example): https://dorvaleqcapital.example/. Many of the general items on this site match what we will need (description of loan programs, FAQ)

Target Market(s)

Real estate investors (generally individuals or small companies with just a few people) who are buying homes, renovating them and then selling them at a profit.

Industry/Entity Type

Finance

Coding

Coded - Design and coding required

Number of Pages Required

5+ page

Colors

Designer to choose colors to be used in the design.

Requirements
Must have
• Minimalist design. Clean lines without too much clutter. Some stock photography is ok but the photos should not be distracting. They should almost fade in to the background so that user can focus on the key information about what our company does instead. We are a finance company, not a design company, so the information about our products will be more interesting to site visitors than the art.
• Some minimalist examples from Snapboard:
• https://www.snapboardia.example/explore/minimalist-web-design/
Nice to have
• If you search in zoovle for "hard money lenders" you will find many examples of web sites from our competition. I have provided a link above to competitor web site that I like a lot.
• I have attached our logo in EPS format. Logo is green. Web site doesn't have to be green but it should be of a color that will work well with the logo.

```html
<!DOCTYPE html>
<html lang="en">
<head>
<meta charset="utf-8">
<title>RTV Finance — Real Estate Lending</title>
<link href="https://fonts.googleapis.com/css2?family=Mulish:wght@400;600;700&family=Open+Sans:wght@400;600;700&display=swap" rel="stylesheet">
<style>
:root{
  --green:#0b5a3a;
  --green-dark:#063d27;
  --green-deep:#04301f;
  --ink:#333333;
  --muted:#6f6f6f;
  --grey-band:#e4e4e4;
  --grey-panel:#7a7a7a;
  --line:#d6d6d6;
  --white:#ffffff;
}
*{margin:0;padding:0;box-sizing:border-box}
html,body{width:1200px;height:3214px;overflow:hidden;background:var(--white)}
body{position:relative;font-family:"Open Sans",Arial,sans-serif;color:var(--ink)}
.abs{position:absolute}
h1,h2,h3,.nav,.brand{font-family:"Mulish","Open Sans",sans-serif}

/* header */
.site-header{left:0;top:0;width:1200px;height:100px;background:var(--white)}
.brand{position:absolute;left:115px;top:30px;display:flex;align-items:center;gap:12px;color:var(--green);font-weight:700;font-size:27px}
.brand-square{width:30px;height:30px;background:var(--green)}
.nav{position:absolute;left:540px;top:54px;display:flex;gap:48px;font-size:16px;color:#555}
.nav a{color:inherit;text-decoration:none}
.nav .current{color:var(--green);font-weight:700}
.chat-btn{position:absolute;left:960px;top:0;width:110px;height:38px;background:var(--green);color:var(--white);font-size:12px;display:flex;align-items:center;justify-content:center;gap:6px}

/* hero */
.hero{left:0;top:100px;width:1200px;height:580px;background:linear-gradient(180deg,#7b9bb0 0%,#4d6a55 35%,#3f5a44 60%,#7f8a76 82%,#8d8f8c 100%)}
.hero-title{position:absolute;left:0;top:205px;width:1200px;text-align:center;color:var(--white);font-size:38px;font-weight:700;line-height:46px}
.hero-btn{position:absolute;left:518px;top:322px;width:160px;height:44px;border:1px solid var(--white);color:var(--white);font-size:16px;display:flex;align-items:center;justify-content:center}
.hero-dots{position:absolute;left:562px;top:537px;display:flex;gap:9px}
.hero-dots span{width:12px;height:12px;border-radius:50%;background:var(--white)}
.hero-dots span:first-child{background:transparent;border:2px solid var(--white)}

/* about */
.about{left:0;top:680px;width:1200px;height:400px}
.section-title{position:absolute;left:0;width:1200px;text-align:center;font-size:30px;font-weight:700;color:#777}
.section-title b{color:var(--green)}
.about-lead{position:absolute;left:290px;top:118px;width:620px;text-align:center;font-size:12px;line-height:20px;color:#777}
.about-item{position:absolute;top:200px;display:flex;gap:14px;font-size:13.5px;line-height:21px;color:#666}
.tick{flex:none;width:26px;height:26px}

/* why */
.why{left:0;top:1080px;width:1200px;height:370px;background:var(--grey-band)}
.why h2{position:absolute;left:0;top:50px;width:1200px;text-align:center;font-size:27px;font-weight:600;color:#333}
.why-item{position:absolute;top:165px;width:150px;text-align:center;font-size:15px;color:#444;line-height:21px}
.why-item svg{display:block;margin:0 auto 20px;width:56px;height:56px}

/* loans */
.loan{top:1450px;height:437px;width:600px;color:var(--white);text-align:center}
.loan-fix{left:0;background:linear-gradient(135deg,#1e6a48,#0b4d31 60%,#0f5738)}
.loan-com{left:600px;background:linear-gradient(135deg,#8a8a8a,#6a6a6a 60%,#7a7a7a)}
.loan svg{position:absolute;left:270px;top:78px}
.loan h3{position:absolute;left:0;top:160px;width:600px;font-size:29px;font-weight:600;line-height:34px}
.loan p{position:absolute;left:145px;width:310px;font-size:12.5px;line-height:20px;color:#e8e8e8}
.loan .btn{position:absolute;left:264px;top:307px;width:140px;height:38px;background:#333;color:var(--white);font-size:15px;display:flex;align-items:center;justify-content:center}
.loan-com .btn{left:785px;left:185px}

/* blogs */
.blogs{left:0;top:1887px;width:1200px;height:518px;background:var(--grey-band)}
.blogs h2{position:absolute;left:125px;top:50px;font-size:29px;font-weight:400;color:#333}
.card{position:absolute;top:110px;width:303px;height:346px;background:var(--white);border:1px solid var(--line)}
.card-img{height:195px}
.card h3{margin:18px 24px 8px;font-size:18px;font-weight:400;color:var(--green)}
.card p{margin:0 24px;font-size:11.5px;line-height:17px;color:#777}
.card .more{display:block;margin:8px 24px;font-size:11.5px;font-weight:700;color:#333}

/* membership */
.members{left:0;top:2405px;width:1200px;height:365px}
.members h2{position:absolute;left:0;top:60px;width:1200px;text-align:center;font-size:30px;font-weight:400;color:var(--green)}
.badge{position:absolute;height:36px;background:#c9c9c9;border-radius:4px}

/* footer */
.footer-shape{left:0;top:2765px}
.footer-brand{position:absolute;left:115px;top:2915px;display:flex;align-items:center;gap:14px;color:var(--white);font-family:"Mulish",sans-serif;font-weight:700;font-size:34px}
.footer-brand .brand-square{width:40px;height:40px;background:var(--white)}
.fcol{position:absolute;top:2870px;color:var(--white)}
.fcol h4{font-family:"Mulish",sans-serif;font-size:19px;font-weight:600;margin-bottom:16px}
.fcol li{list-style:none;font-size:14px;line-height:31px;color:#e4eee8}
.contact li{display:flex;align-items:center;gap:14px}
.socials{position:absolute;left:623px;top:3022px;display:flex;gap:8px}
.socials span{width:29px;height:29px;border:1.5px solid var(--white);border-radius:50%}
.copyright{left:0;top:3145px;width:1200px;height:69px;background:var(--green-deep);color:#cfd8d3;font-size:12px;padding-left:418px;line-height:69px}
</style>
</head>
<body>

<header class="abs site-header">
  <div class="brand"><span class="brand-square"></span>RTV Finance</div>
  <nav class="nav">
    <a class="current">Home</a><a>About Us</a><a>Loans</a><a>Resources</a><a>Contact Us</a>
  </nav>
  <div class="chat-btn">
    <svg width="14" height="12" viewBox="0 0 14 12"><path d="M7 0C3 0 0 2.3 0 5.2c0 1.5.8 2.8 2 3.7L1.4 12l3.4-1.9c.7.2 1.4.3 2.2.3 4 0 7-2.3 7-5.2S11 0 7 0z" fill="#fff"/></svg>
    Chat Now
  </div>
</header>

<section class="abs hero" role="img" aria-label="Photo of a suburban family house with lawn and driveway, softly faded">
  <h1 class="hero-title">Local Real Estate Experts lending<br>to local Real Estate Investors</h1>
  <div class="hero-btn">Read More</div>
  <div class="hero-dots"><span></span><span></span><span></span><span></span></div>
</section>

<section class="abs about">
  <h2 class="section-title" style="top:62px">About <b>RTV Finance</b></h2>
  <p class="about-lead">ullamcorper est eget tempor cursus neque mi consectetuer mi a ultricies massa est sed nisl Class aptent taciti sociosqu ad litora torquent per conubia nostra per inceptos hymenaeo</p>
  <div class="about-item" style="left:170px;width:300px">
    <svg class="tick" viewBox="0 0 26 26"><circle cx="13" cy="13" r="13" fill="#0b5a3a"/><path d="M7 13.5l4 4 8-8" stroke="#fff" stroke-width="3" fill="none"/></svg>
    <span>RTV Finance is a local business with local knowledge and strong industry relationships. A partner with a wide network who offers value added services.</span>
  </div>
  <div class="about-item" style="left:515px;width:330px">
    <svg class="tick" viewBox="0 0 26 26"><circle cx="13" cy="13" r="13" fill="#0b5a3a"/><path d="M7 13.5l4 4 8-8" stroke="#fff" stroke-width="3" fill="none"/></svg>
    <span>RTV has an established pool of experienced investors available for your real estate investment needs</span>
  </div>
  <div class="about-item" style="left:870px;width:240px">
    <svg class="tick" viewBox="0 0 26 26"><circle cx="13" cy="13" r="13" fill="#0b5a3a"/><path d="M7 13.5l4 4 8-8" stroke="#fff" stroke-width="3" fill="none"/></svg>
    <span>Loans offered<br>(Fix and Flip, Commercial)</span>
  </div>
</section>

<section class="abs why">
  <h2>Why Borrow from RTV</h2>
  <div class="why-item" style="left:127px">
    <svg viewBox="0 0 56 56"><circle cx="28" cy="24" r="16" fill="#0b5a3a"/><rect x="20" y="38" width="16" height="12" fill="#0b5a3a"/><circle cx="28" cy="24" r="6" fill="none" stroke="#fff" stroke-width="3"/></svg>
    Experts</div>
  <div class="why-item" style="left:285px">
    <svg viewBox="0 0 56 56" fill="none" stroke="#0b5a3a" stroke-width="3"><path d="M18 38c4-16 14-26 28-28-2 14-12 24-28 28z"/><circle cx="34" cy="22" r="4"/><path d="M18 38l-8 8M14 30l-6 2M26 42l-2 6"/></svg>
    Fast Approval</div>
  <div class="why-item" style="left:450px">
    <svg viewBox="0 0 56 56"><path d="M22 6h12l-3 8h-6z" fill="#0b5a3a"/><path d="M25 14h6l5 28-8 10-8-10z" fill="#0b5a3a"/></svg>
    Professional</div>
  <div class="why-item" style="left:603px">
    <svg viewBox="0 0 56 56" fill="none" stroke="#0b5a3a" stroke-width="3"><path d="M2 20l10-4 8 4 8-4 8 4 10-4 8 4M12 16v18l12 10 8-4 12-8V16"/><path d="M20 30l8 8M26 26l8 8"/></svg>
    A Partner</div>
  <div class="why-item" style="left:740px">
    <svg viewBox="0 0 56 56" fill="none" stroke="#0b5a3a" stroke-width="3"><rect x="8" y="10" width="34" height="38"/><rect x="14" y="16" width="34" height="36"/><path d="M20 30l8 8 18-22"/></svg>
    Selective</div>
  <div class="why-item" style="left:895px">
    <svg viewBox="0 0 56 56"><path d="M30 4h20v20L26 50 6 30z" fill="#0b5a3a"/><circle cx="42" cy="12" r="3" fill="#fff"/><path d="M32 22c-2-2-7-2-7 1s7 2 7 5-5 3-7 1M28 18v2M28 32v2" stroke="#fff" stroke-width="2.2" fill="none"/></svg>
    Competitive Rates<br>and Fees</div>
</section>

<section class="abs loan loan-fix" role="img" aria-label="Photo of a smiling investor holding house keys, under a green tint">
  <svg width="60" height="60" viewBox="0 0 60 60" fill="#fff"><rect x="8" y="6" width="30" height="40"/><rect x="22" y="14" width="30" height="40" stroke="#0b5a3a" stroke-width="2"/><text x="10" y="32" font-size="20" font-family="Mulish,sans-serif" fill="#0b5a3a" font-weight="700">%</text></svg>
  <h3>Fix and Flip Loans</h3>
  <p style="top:210px">ullamcorper est eget tempor cursus neque mi consectetuer mi a ultricies massa est sed nisl Class aptent taciti sociosqu ad litora torquent per conubia</p>
  <div class="btn">Read More</div>
</section>
<section class="abs loan loan-com" role="img" aria-label="Photo of a large house in grey tones">
  <svg width="60" height="60" viewBox="0 0 60 60" fill="#fff"><rect x="16" y="4" width="28" height="52"/><g fill="#7a7a7a"><rect x="21" y="10" width="6" height="6"/><rect x="33" y="10" width="6" height="6"/><rect x="21" y="22" width="6" height="6"/><rect x="33" y="22" width="6" height="6"/><rect x="21" y="34" width="6" height="6"/><rect x="33" y="34" width="6" height="6"/><rect x="26" y="46" width="8" height="10"/></g></svg>
  <h3>Commercial Hard<br>Money Loans</h3>
  <p style="top:240px">ullamcorper est eget tempor cursus neque mi consectetuer mi a ultricies massa est sed nisl Class aptent tacio</p>
  <div class="btn" style="left:185px">Read More</div>
</section>

<section class="abs blogs">
  <h2>Latest Blogs</h2>
  <article class="card" style="left:125px">
    <div class="card-img" role="img" aria-label="Photo of a hand passing a money bag at sunset" style="background:linear-gradient(135deg,#f1b23a,#c9731d 55%,#8a5a2a)"></div>
    <h3>Project Tittle here</h3>
    <p>netus et malesuada fames ac turpis egestas Cras id elit integer quis urna Ut ante enim dapibus malesuada fringilla eu cond</p>
    <span class="more">READ MORE</span>
  </article>
  <article class="card" style="left:445px">
    <div class="card-img" role="img" aria-label="Photo of stacked gold coins" style="background:linear-gradient(135deg,#f3efe6,#c8a25a 55%,#8e6a2e)"></div>
    <h3>Project Tittle here</h3>
    <p>netus et malesuada fames ac turpis egestas Cras id elit integer quis urna Ut ante enim dapibus malesuada fringilla eu cond</p>
    <span class="more">READ MORE</span>
  </article>
  <article class="card" style="left:768px">
    <div class="card-img" role="img" aria-label="Photo of a small model house on grass" style="background:linear-gradient(180deg,#dfe8ee,#a9c48a 45%,#4f8a2e)"></div>
    <h3>Project Tittle here</h3>
    <p>netus et malesuada fames ac turpis egestas Cras id elit integer quis urna Ut ante enim dapibus malesuada fringilla eu cond</p>
    <span class="more">READ MORE</span>
  </article>
</section>

<section class="abs members">
  <h2>Industry Membership</h2>
  <div class="badge" style="left:165px;top:150px;width:70px"></div>
  <div class="badge" style="left:270px;top:150px;width:120px"></div>
  <div class="badge" style="left:430px;top:150px;width:105px"></div>
  <div class="badge" style="left:578px;top:150px;width:118px"></div>
  <div class="badge" style="left:758px;top:150px;width:92px"></div>
  <div class="badge" style="left:878px;top:150px;width:210px"></div>
  <div class="badge" style="left:168px;top:245px;width:64px"></div>
  <div class="badge" style="left:283px;top:245px;width:108px"></div>
  <div class="badge" style="left:445px;top:245px;width:100px"></div>
  <div class="badge" style="left:600px;top:245px;width:100px"></div>
  <div class="badge" style="left:776px;top:245px;width:70px"></div>
  <div class="badge" style="left:924px;top:245px;width:110px"></div>
</section>

<svg class="abs footer-shape" width="1200" height="380" viewBox="0 0 1200 380">
  <defs><linearGradient id="fg" x1="0" y1="0" x2="0" y2="1"><stop offset="0" stop-color="#0b5a3a"/><stop offset="1" stop-color="#063d27"/></linearGradient></defs>
  <path d="M0 62 L200 0 L735 0 L1200 62 L1200 380 L0 380 Z" fill="url(#fg)"/>
</svg>
<div class="footer-brand"><span class="brand-square"></span>RTV Finance</div>
<div class="fcol" style="left:435px"><h4>Quick Links</h4><ul><li>Home</li><li>About Us</li><li>Loans</li><li>Resources</li></ul></div>
<div class="fcol" style="left:628px"><h4>Resources</h4><ul><li>Blogs</li><li>Testimonials</li><li>Contact Us</li></ul></div>
<div class="fcol contact" style="left:838px"><h4>Contact Us</h4>
  <ul>
    <li><svg width="14" height="18" viewBox="0 0 14 18"><path d="M7 0a7 7 0 0 0-7 7c0 5 7 11 7 11s7-6 7-11a7 7 0 0 0-7-7z" fill="#fff"/><circle cx="7" cy="7" r="2.5" fill="#0b5a3a"/></svg>48 Alder Crest Lane #4B</li>
    <li style="padding-left:28px">Brookfield 20917</li>
    <li><svg width="16" height="16" viewBox="0 0 16 16"><path d="M3 1l3 3-2 2c1 2 4 5 6 6l2-2 3 3-2 2C7 15 1 9 1 3z" fill="none" stroke="#fff" stroke-width="1.4"/></svg>555.014.7730</li>
    <li><svg width="16" height="14" viewBox="0 0 16 14"><rect x="1" y="1" width="14" height="12" fill="none" stroke="#fff" stroke-width="1.4"/><path d="M1 1l7 6 7-6" fill="none" stroke="#fff" stroke-width="1.4"/></svg>info@rtvfinance.example</li>
  </ul>
</div>
<div class="socials"><span></span><span></span><span></span><span></span></div>
<div class="abs copyright">© 2017 Company Name &nbsp;All right reserved &nbsp;Term of Use</div>

</body>
</html>
```